Business Card Design Project

We have recently completed CraftHive projects for a new logo and wesbite.
We now require new business cards.
We hand out very little printed material to clients as all information is online. When we do hand out something, like a business card, we want it to have real impact and make a statement about the quality and professionalism of our company.
We have an idea of what we want our card to look like but we want a designer to make sure they have impact and look great.
Our requirements are…
Size: 85mm X 55mm - Landscape
Front of card: Logo plus the following contact information.
Dennis Marlow
Operations Manager
Phone +44(0) 1632 xxx xxx
Mobile +44(0) 7700 xxx xxx
Email denmo@korvantix.example
Address 17 Pellick Row, Aberdeen AB12 9QZ
Website www.korvantix.example
How you layout the front of the card is up to you, we would like to see some different ideas. Attached are two versions of our logo that may be used.
Back of card: We would like this to be simple but again have impact. Our current thought is to have the logo or just the large W design from the logo in white against a dark background, perhaps made up from the dark green in the logo.
The logos are attached so you can see the colours in them but the dark ones are..
Dark Blue = C:88, M:55, Y:44, K:28
Dark Green = C:87, M:53, Y:50, K:50
We sometimes also use a bright orange as an accent or highlight colour…
Orange: = C:0, M:39, Y:94, K:0

```html
<!DOCTYPE html>
<html lang="en">
<head>
<meta charset="utf-8">
<title>Korvantix business cards</title>
<link rel="stylesheet" href="https://fonts.googleapis.com/css2?family=Open+Sans:wght@400;600;700&display=swap">
<style>
  :root {
    --backdrop: #e9e7e3;
    --card-white: #ffffff;
    --teal-dark: #21434a;
    --olive: #7a8f5a;
    --ink: #2f3f44;
    --ink-strong: #21434a;
    --rule: #b9c0c2;
    --shadow: rgba(0, 0, 0, 0.28);
  }
  * { box-sizing: border-box; margin: 0; padding: 0; }
  html, body {
    width: 1200px; height: 800px; overflow: hidden;
    background: var(--backdrop);
    font-family: "Open Sans", Arial, sans-serif;
  }
  .stage { position: relative; width: 1200px; height: 800px; }
  .card {
    position: absolute; width: 502px; height: 323px;
    border-radius: 14px;
    box-shadow: 0 3px 8px var(--shadow);
    overflow: hidden;
  }
  .card--front { left: 76px; top: 67px; background: var(--card-white); }
  .card--back-dark { left: 610px; top: 67px; background: var(--teal-dark); }
  .card--back-gradient {
    left: 86px; top: 408px; width: 500px;
    background: linear-gradient(90deg, var(--teal-dark) 0%, var(--olive) 100%);
  }
  .card--back-light { left: 610px; top: 408px; background: var(--card-white); }

  .brand {
    position: absolute; left: 0; right: 0; top: 55px;
    text-align: center;
    font-weight: 700; font-size: 42px; letter-spacing: 3px;
    color: var(--ink-strong);
  }
  .identity {
    position: absolute; right: 279px; top: 183px;
    text-align: right; color: var(--ink);
    font-size: 13px; line-height: 20px;
  }
  .identity__name {
    font-weight: 700; font-size: 16px; color: var(--ink-strong);
    line-height: 22px; text-transform: uppercase;
  }
  .identity__role { margin-bottom: 8px; }
  .divider {
    position: absolute; left: 251px; top: 178px;
    width: 1px; height: 84px; background: var(--rule);
  }
  .contacts {
    position: absolute; left: 267px; top: 183px;
    list-style: none; color: var(--ink); font-size: 13px;
  }
  .contacts li { display: flex; align-items: center; height: 20.5px; }
  .contacts svg { width: 11px; height: 11px; margin-right: 5px; fill: var(--ink-strong); }

  .back-name {
    position: absolute; left: 0; right: 0; top: 112px;
    text-align: center; font-weight: 700; font-size: 54px; letter-spacing: 4px;
    color: #ffffff;
  }
  .card--back-light .back-name { color: var(--teal-dark); }
  .back-url {
    position: absolute; left: 0; right: 0; top: 266px;
    text-align: center; font-size: 15px; letter-spacing: 3px; color: #ffffff;
  }
  .card--back-light .back-url { color: var(--ink-strong); }
</style>
</head>
<body>
<main class="stage">
  <section class="card card--front">
    <div class="brand">KORVANTIX</div>
    <div class="identity">
      <div class="identity__name">Dennis Marlow</div>
      <div class="identity__role">Operations Manager</div>
      <div>17 Pellick Row,</div>
      <div>Aberdeen AB12 9QZ</div>
    </div>
    <div class="divider"></div>
    <ul class="contacts">
      <li><svg viewBox="0 0 12 12" aria-hidden="true"><path d="M3 1l2 2.5-1 1.2c.6 1.3 1.6 2.3 2.9 2.9L8 6.6 10.5 8.6 9.6 10.6C5.5 10.4 1.6 6.5 1.4 2.4Z"/></svg>+44(0) 1632 xxx xxx</li>
      <li><svg viewBox="0 0 12 12" aria-hidden="true"><path d="M3.5 0.5h5v11h-5Zm1 1.2v7h3v-7Z"/></svg>+44(0) 7700 xxx xxx</li>
      <li><svg viewBox="0 0 12 12" aria-hidden="true"><path d="M0.5 2.5h11v7h-11Zm1 1 4.5 3 4.5-3v-0.2h-9Z"/></svg>denmo@korvantix.example</li>
      <li><svg viewBox="0 0 12 12" aria-hidden="true"><path d="M6 0.5a5.5 5.5 0 1 0 0.01 0Zm0 1.2c.8.9 1.3 2.3 1.4 3.7H4.6C4.7 4 5.2 2.6 6 1.7Zm-1.4 4.9h2.8C7.3 8 6.8 9.4 6 10.3 5.2 9.4 4.7 8 4.6 6.6Z"/></svg>www.korvantix.example</li>
    </ul>
  </section>

  <section class="card card--back-dark">
    <div class="back-name">KORVANTIX</div>
    <div class="back-url">www.korvantix.example</div>
  </section>

  <section class="card card--back-gradient">
    <div class="back-name">KORVANTIX</div>
    <div class="back-url">www.korvantix.example</div>
  </section>

  <section class="card card--back-light">
    <div class="back-name">KORVANTIX</div>
    <div class="back-url">www.korvantix.example</div>
  </section>
</main>
</body>
</html>
```